Maple Beacon Website

We are starting a marketing company and to do that we need a website! We want a website that will inspire and persuade to bring out the awesomeness in our clients.
What we want to see:
- Inspirational and persuasive imagery that relate to Branding.
- No cliche images eg. business man, suits and hand shakes
- We want to transform and educate our clients.
- We want to show them the path and would like our website to really act as a guide that guides them step by step through our process.
- We want the portray that we are an investment but not have a pretentious way to it. We put our heart into every project and that is how we treat our clients.
-When you submit your design please include what platform you have created for. Preference would be Wordpress or Joobla.

We have included the psd file for the wire frame, logo files, font files, site map and a link to a video we create to give you more information on what we would like to see. http://clipvault.example/t/qk82LmZpr

Feel free to make small modification to the logos if you think it will improve it. Your creativity and advice is most welcome.
Updates

One thing we forgot. We would like to have our contact information near the top of the website as well as at the bottom.  Here is out contact info:

Email: info@maplebeacon.example
Phone: 587-555-0142

Project Deadline Extended
Reason: As we are new with the platform and that we want to optimize our results, we decided to extend the deadline by 15 days. Thanks!

Target Market(s)

28-60, Male and Female, Oil field, Local Businesses, Dentists, Chiropractors, Hair salon, Construction/Renovation, Events etc

Industry/Entity Type

Investment

Requirements
Must have
• - 4 Inspirational and persuasive Imagery for the top portion of the website
- Must have a feel as if your not on a website an example of this is linked below.
http://www.artbidhub.example/design/402957/web-design-by-lena-torvik
Nice to have
• - Creative advice from you.
- Creative buttons for Get Free Quote and Subscribe buttons. Something out of the box that draws peoples attention. eg. a 'B' button. Just and example but still something related to branding.
Should not have
• No Cliches

```html
<!DOCTYPE html>
<html lang="en">
<head>
<meta charset="utf-8">
<title>Maple Beacon</title>
<link rel="stylesheet" href="https://fonts.googleapis.com/css2?family=Fredoka:wght@500;600&family=Nunito+Sans:wght@400;600;700&display=swap">
<style>
:root{
  --green:#8cc03a;
  --grey-tab:#8e8e8e;
  --grey-text:#7b7b7b;
  --body-text:#555;
  --white:#fff;
  --caption:rgba(40,40,40,.78);
  --icon:#5d5d5d;
}
*{box-sizing:border-box;margin:0;padding:0}
html,body{width:1200px;height:823px;overflow:hidden}
body{position:relative;font-family:"Nunito Sans",sans-serif;color:var(--body-text);
  background:radial-gradient(ellipse 520px 320px at 560px 560px,#fff 0%,#ececec 70%,#e6e6e6 100%)}
.abs{position:absolute}
.top-bar{left:0;top:0;width:1200px;height:35px;background:var(--green)}
.top-contact{right:132px;top:9px;display:flex;gap:14px;color:var(--white);font-size:13px;align-items:center}
.top-contact span{display:flex;align-items:center;gap:5px}
.top-contact .sep{width:1px;height:20px;border-left:1px dotted rgba(255,255,255,.6)}
.brand-panel{left:130px;top:0;width:227px;height:336px;background:linear-gradient(#fff,#ececec)}
.logo{left:144px;top:40px;display:flex;align-items:center;gap:8px}
.logo-mark{width:20px;height:20px;border-radius:50%;background:#8a8a8a}
.logo-name{font-weight:700;font-size:21px;color:#8a8a8a;letter-spacing:.5px}
.side-nav{left:123px;top:125px;list-style:none;font-family:"Fredoka",sans-serif;font-weight:600;font-size:16px;color:var(--grey-text)}
.side-nav li{height:29px;padding-left:18px;line-height:26px}
.side-nav li.active{width:199px;height:25px;line-height:25px;background:var(--green);color:var(--white);border-radius:0 13px 13px 0;margin-bottom:4px}
.connect-title{left:130px;top:302px;width:227px;text-align:center;font-family:"Fredoka",sans-serif;font-weight:600;font-size:19px;color:var(--green)}
.tabs{left:357px;top:36px;height:41px}
.tab{position:absolute;top:0;height:41px;font-family:"Fredoka",sans-serif;font-weight:600;font-size:17px;color:#d9d9d9;text-align:center;line-height:41px;background:var(--grey-tab)}
.tab.active{background:var(--green);color:var(--white)}
.hero{left:357px;top:77px;width:713px;height:259px;background:linear-gradient(120deg,#cfd8e2 0%,#e8ecf0 55%,#d9dde0 100%)}
.caption{left:727px;top:232px;width:350px;height:71px;background:var(--caption);color:var(--white);font-size:12.5px;line-height:14px;padding:9px 12px}
.band{left:123px;top:336px;width:954px;height:44px;background:repeating-linear-gradient(45deg,#737373 0 2px,#6a6a6a 2px 4px)}
.socials{left:174px;top:345px;display:flex;gap:5px}
.socials i{display:block;width:27px;height:25px;border-radius:3px;background:var(--icon)}
.band-divider{left:356px;top:347px;height:20px;border-left:1px dotted #bbb}
.news-label{left:381px;top:348px;font-family:"Fredoka",sans-serif;font-weight:600;font-size:14.5px;color:var(--white)}
.email-field{left:728px;top:348px;width:192px;height:22px;border-radius:11px;background:var(--white);border:1px solid #ccc;font-size:11px;color:#aaa;padding:4px 10px}
.subscribe{left:932px;top:347px;width:98px;height:23px;background:linear-gradient(#e8eaee,#b9bec7);clip-path:polygon(8% 0,100% 0,92% 100%,0 100%);font-family:"Fredoka",sans-serif;font-weight:600;font-size:13px;color:#555;text-align:center;line-height:24px}
.content{left:291px;top:390px;width:620px;font-size:12.3px;line-height:16px}
.content h1{font-family:"Fredoka",sans-serif;font-weight:600;font-size:24px;color:var(--green);margin-bottom:2px;line-height:28px}
.content p{margin-bottom:15px}
.content p.tight{margin-bottom:3px}
.content p.cta{font-size:13.3px;margin-top:-3px;padding-left:2px}
.cta a{color:var(--green);font-weight:700;text-decoration:none}
.footer{left:0;top:719px;width:1200px;height:77px;background:repeating-linear-gradient(45deg,#5a5a5a 0 2px,#515151 2px 4px)}
.footer-contact{left:132px;top:733px;color:var(--white);font-size:15px;line-height:25px}
.footer-contact div{display:flex;align-items:center;gap:7px}
.footer-logo{right:132px;top:745px}
.footer-logo .logo-name{font-size:18px;color:#bdbdbd}
.copyright{left:0;top:796px;width:1200px;height:27px;background:var(--green);color:var(--white);font-size:12px;line-height:27px;padding-left:132px}
</style>
</head>
<body>
<div class="abs top-bar"></div>
<div class="abs top-contact">
  <span><svg width="13" height="13" viewBox="0 0 24 24"><path fill="#fff" d="M6.6 10.8a15 15 0 0 0 6.6 6.6l2.2-2.2c.3-.3.7-.4 1-.2 1.1.4 2.3.6 3.6.6.6 0 1 .4 1 1V20c0 .6-.4 1-1 1A17 17 0 0 1 3 4c0-.6.4-1 1-1h3.5c.6 0 1 .4 1 1 0 1.3.2 2.5.6 3.6.1.3 0 .7-.2 1z"/></svg>587-555-0142</span>
  <span class="sep"></span>
  <span><svg width="16" height="12" viewBox="0 0 16 12"><rect x="0.5" y="0.5" width="15" height="11" fill="#fff"/><path d="M1 1l7 6 7-6" fill="none" stroke="#8cc03a" stroke-width="1.4"/></svg>info@maplebeacon.example</span>
</div>

<div class="abs brand-panel"></div>
<div class="abs logo"><span class="logo-mark"></span><span class="logo-name">MAPLE BEACON</span></div>

<ul class="abs side-nav">
  <li class="active">STRATEGY</li>
  <li>PORTFOLIO</li>
  <li>ABOUT US</li>
  <li>CONTACT US</li>
  <li>BLOG</li>
</ul>
<div class="abs connect-title">Connect With Us:</div>

<nav class="abs tabs">
  <div class="tab active" style="left:0;width:166px">BRANDING</div>
  <div class="tab" style="left:189px;width:166px">BE FOUND</div>
  <div class="tab" style="left:374px;width:156px">CONNECT</div>
  <div class="tab" style="left:548px;width:165px">GET GROWING</div>
</nav>

<div class="abs hero" role="img" aria-label="Banner photo: a hand lifting an orange paper figure above a row of blue paper figures"></div>
<div class="abs caption">Lorem Ipsum is simply dummy text of the printing and typesetting industry. Lorem Ipsum has been the industry’s standard dummy text ever since the 1500s, when an unknown printer took a galley...</div>

<div class="abs band"></div>
<div class="abs socials" aria-label="Social links"><i></i><i></i><i></i><i></i></div>
<div class="abs band-divider"></div>
<div class="abs news-label">Get Tips &amp; Tricks!&nbsp;&nbsp;&nbsp;Subscribe To Our Newsletter!</div>
<div class="abs email-field">Enter Your Email...</div>
<div class="abs subscribe">SUBSCRIBE</div>

<main class="abs content">
  <h1>WELCOME TO MAPLE BEACON!</h1>
  <p>Lorem Ipsum is simply dummy text of the printing and typesetting industry. Lorem Ipsum has been the industry’s standard dummy text ever since the 1500s, when an unknown printer took a galley of type and scrambled it to make a type specimen book.</p>
  <p>It has survived not only five centuries, but also the leap into electronic typesetting, remaining essentially unchanged.</p>
  <p class="tight">It was popularised in the 1960s with the release of Lettrafix sheets containing Lorem Ipsum passages, and more recently with desktop publishing software like Pagewright Studio including Lorem Ipsum.</p>
  <p>Lorem Ipsum is simply dummy text of the printing and typesetting industry. Lorem Ipsum has been the industry’s standard dummy text ever since the 1500s, when an unknown printer took a galley of type and scrambled it to make a type specimen book.</p>
  <p>It was popularised in the 1960s with the release of Lettrafix sheets containing.</p>
  <p class="cta">If you would like to have more information on how we can help you achive your goals. You can visit our <a href="#">STRATEGY</a> page or&nbsp; simply get a <a href="#">FREE QUOTE!</a>.</p>
</main>

<footer class="abs footer"></footer>
<div class="abs footer-contact">
  <div><svg width="20" height="20" viewBox="0 0 24 24"><path fill="#ddd" d="M6.6 10.8a15 15 0 0 0 6.6 6.6l2.2-2.2c.3-.3.7-.4 1-.2 1.1.4 2.3.6 3.6.6.6 0 1 .4 1 1V20c0 .6-.4 1-1 1A17 17 0 0 1 3 4c0-.6.4-1 1-1h3.5c.6 0 1 .4 1 1 0 1.3.2 2.5.6 3.6.1.3 0 .7-.2 1z"/></svg>587-555-0142</div>
  <div><svg width="20" height="15" viewBox="0 0 16 12"><rect x="0.5" y="0.5" width="15" height="11" fill="#ddd"/><path d="M1 1l7 6 7-6" fill="none" stroke="#575757" stroke-width="1.4"/></svg>info@maplebeacon.example</div>
</div>
<div class="abs footer-logo"><div class="logo-name">MAPLE BEACON</div></div>
<div class="abs copyright">Copyright © 2013 Maple Beacon, All Rights Reserved.</div>
</body>
</html>
```